Salon and Spa Distributor Business Card

Need a business card. We are are distributor in the salon and spa industry. We identify with natural beauty. Need a card with:
Company Name: Petal Quarry"
Title: "President & CEO"
Address
Company Phone number
email
website
Tag Line:" The Professional Salon Source"

Industry/Entity Type

Business

Contact Information for Business Card

Name: Dov Strommen
Title: "President & CEO"
Address: 31 Harlow Ln, Bexmoor, NJ 07813
Company Phone number: 800-463-5918
email: dovstrommen@petalquarry.example
website: www.petalquarry.example

Requirements
Should not have
• No black backgrounds

```html
<!DOCTYPE html>
<html lang="en">
<head>
<meta charset="utf-8">
<title>Petal Quarry Business Card</title>
<link rel="stylesheet" href="https://fonts.googleapis.com/css2?family=Questrial&family=Mulish:wght@700&display=swap">
<style>
  :root {
    --page: #ffffff;
    --card: #f3f0e7;
    --green: #3f8f42;
    --green-bright: #4fa24f;
    --green-deep: #1f6b2c;
    --ink: #2e3430;
  }
  html, body {
    margin: 0;
    padding: 0;
    width: 1200px;
    height: 900px;
    overflow: hidden;
    background: var(--page);
  }
  .canvas {
    position: relative;
    width: 1200px;
    height: 900px;
    font-family: "Questrial", "Century Gothic", sans-serif;
  }
  .card {
    position: absolute;
    top: 271px;
    width: 458px;
    height: 282px;
    background: var(--card);
    border-radius: 13px;
    box-shadow: 2px 3px 5px rgba(0,0,0,0.35);
    overflow: hidden;
  }
  .card--front { left: 137px; }
  .card--back  { left: 626px; }

  .wordmark {
    position: absolute;
    margin: 0;
    font-family: "Questrial", "Century Gothic", sans-serif;
    font-weight: 400;
    color: var(--green);
    white-space: nowrap;
    line-height: 1;
  }
  .card--front .wordmark {
    left: 28px;
    top: 28px;
    font-size: 37px;
  }
  .brand-art {
    position: absolute;
    right: 0;
    top: 0;
    width: 190px;
    height: 282px;
    background: linear-gradient(200deg, var(--green-bright) 0%, var(--green) 45%, var(--green-deep) 100%);
    opacity: 0.9;
    -webkit-mask-image: linear-gradient(90deg, transparent 0%, #000 45%);
            mask-image: linear-gradient(90deg, transparent 0%, #000 45%);
  }
  .holder-name {
    position: absolute;
    left: 27px;
    top: 95px;
    margin: 0;
    font-family: "Mulish", "Century Gothic", sans-serif;
    font-weight: 700;
    font-size: 23px;
    color: var(--green);
    line-height: 1;
  }
  .holder-title {
    position: absolute;
    left: 28px;
    top: 125px;
    margin: 0;
    font-size: 14px;
    color: var(--ink);
  }
  .contact-list {
    position: absolute;
    left: 27px;
    top: 156px;
    margin: 0;
    padding: 0;
    list-style: none;
    font-size: 13.5px;
    color: var(--ink);
  }
  .contact-list li {
    display: flex;
    align-items: center;
    height: 17px;
  }
  .contact-icon {
    width: 11px;
    height: 11px;
    margin-right: 5px;
    flex: none;
  }
  .address {
    position: absolute;
    left: 27px;
    top: 220px;
    margin: 0;
    font-style: normal;
    font-size: 14px;
    line-height: 17px;
    color: var(--ink);
  }

  .brand-dot {
    position: absolute;
    left: 104px;
    top: 125px;
    width: 34px;
    height: 34px;
    border-radius: 50%;
    background: var(--green);
  }
  .card--back .wordmark {
    left: 182px;
    top: 128px;
    font-size: 27px;
  }
  .tagline {
    position: absolute;
    left: 0;
    right: 0;
    top: 224px;
    margin: 0;
    text-align: center;
    font-size: 16px;
    color: var(--ink);
  }
</style>
</head>
<body>
<div class="canvas">

  <section class="card card--front" aria-label="Business card front">
    <p class="wordmark">Petal Quarry</p>
    <div class="brand-art" role="img" aria-label="Green brand decoration area"></div>
    <h1 class="holder-name">Dov Strommen</h1>
    <p class="holder-title">President &amp; CEO</p>
    <ul class="contact-list">
      <li>
        <svg class="contact-icon" viewBox="0 0 12 12" aria-hidden="true">
          <path fill="#3f8f42" d="M1 4.2C1 2.6 3 1.5 6 1.5s5 1.1 5 2.7v.8H8.4V3.8H3.6V5H1zM3 5.6h6l1.5 4.9H1.5z"/>
        </svg>
        800-463-5918
      </li>
      <li>
        <svg class="contact-icon" viewBox="0 0 12 12" aria-hidden="true">
          <rect x="1" y="2.5" width="10" height="7" fill="#3f8f42"/>
          <path d="M1 2.8 6 6.6l5-3.8" fill="none" stroke="#f3f0e7" stroke-width="1"/>
        </svg>
        dovstrommen@petalquarry.example
      </li>
      <li>
        <svg class="contact-icon" viewBox="0 0 12 12" aria-hidden="true">
          <circle cx="6" cy="6" r="5" fill="#3f8f42"/>
          <path d="M3.5 3.5c1 .3 1.4 1.2 1 2s.4 1.6 1.2 1.4M7.5 2.2c-.4 1 .3 1.6 1.3 1.5M8.8 7.2c-.8.2-1.2 1-.9 2" fill="none" stroke="#f3f0e7" stroke-width="0.9"/>
        </svg>
        www.petalquarry.example
      </li>
    </ul>
    <address class="address">31 Harlow Ln,<br>Bexmoor, NJ 07813</address>
  </section>

  <section class="card card--back" aria-label="Business card back">
    <span class="brand-dot" aria-hidden="true"></span>
    <p class="wordmark">Petal Quarry</p>
    <p class="tagline">The Professional Salon Source</p>
  </section>

</div>
</body>
</html>
```